business card deign

Logo needs the following on it.
1. attached logo
2. Tagline - "If it keeps a drink cold or the party going...we do it!"
3. Name- Dalton Pikes, Founder and CPO
4. Address - 412 E. Carver Avenue, Ste 2207, Tampa, FL. 33917
5. Phone - 555.318.4726

```html
<!DOCTYPE html>
<html lang="en">
<head>
<meta charset="utf-8">
<title>Hopwell Business Card</title>
<link rel="stylesheet" href="https://fonts.googleapis.com/css2?family=Roboto+Condensed:wght@400;700&family=Arimo:wght@400&display=swap">
<style>
  :root {
    --backdrop: #2b2b2d;
    --card-dark: #141414;
    --card-light: #ffffff;
    --brand-mark: #3a3a3a;
    --emblem-light: #3b3b3b;
    --emblem-dark: #1a1a1a;
    --tagline: #e9e9e9;
    --ink: #111111;
  }
  html, body {
    margin: 0;
    padding: 0;
    width: 900px;
    height: 1200px;
    overflow: hidden;
    background: var(--backdrop);
  }
  .canvas {
    position: relative;
    width: 900px;
    height: 1200px;
  }
  .card {
    position: absolute;
    left: 135px;
    width: 630px;
    height: 358px;
    box-sizing: border-box;
  }
  .card-front {
    top: 214px;
    background: var(--card-dark);
  }
  .card-back {
    top: 628px;
    background: var(--card-light);
  }
  .emblem-area {
    position: absolute;
    left: 202px;
    top: 78px;
    width: 204px;
    height: 150px;
    border-radius: 6px;
    background: linear-gradient(200deg, var(--emblem-light) 0%, var(--emblem-dark) 85%);
  }
  .brand-name {
    position: absolute;
    left: 0;
    right: 0;
    top: 236px;
    margin: 0;
    text-align: center;
    font-family: "Roboto Condensed", sans-serif;
    font-weight: 700;
    font-size: 50px;
    letter-spacing: 20px;
    text-indent: 20px;
    color: var(--brand-mark);
    line-height: 1;
  }
  .tagline {
    position: absolute;
    left: 0;
    right: 0;
    top: 303px;
    margin: 0;
    text-align: center;
    font-family: "Roboto Condensed", sans-serif;
    font-weight: 400;
    font-size: 15.5px;
    letter-spacing: 1.2px;
    color: var(--tagline);
  }
  .identity {
    position: absolute;
    right: 332px;
    top: 150px;
    text-align: right;
    color: var(--ink);
  }
  .person-name {
    margin: 0;
    font-family: "Roboto Condensed", sans-serif;
    font-weight: 700;
    font-size: 31px;
    line-height: 1;
  }
  .person-role {
    margin: 9px 0 0;
    font-family: "Arimo", sans-serif;
    font-size: 14px;
  }
  .divider {
    position: absolute;
    left: 314px;
    top: 144px;
    width: 2px;
    height: 71px;
    background: var(--ink);
  }
  .contact {
    position: absolute;
    left: 331px;
    top: 140px;
    font-family: "Arimo", sans-serif;
    color: var(--ink);
  }
  .phone {
    display: flex;
    align-items: center;
    gap: 6px;
    margin: 0;
    font-size: 18px;
    letter-spacing: 1px;
  }
  .phone svg { width: 11px; height: 11px; fill: var(--ink); }
  .address {
    margin: 9px 0 0;
    font-size: 14px;
    line-height: 25px;
    font-style: normal;
  }
</style>
</head>
<body>
  <main class="canvas">
    <section class="card card-front">
      <div class="emblem-area" role="img" aria-label="Brand emblem: embossed dark silhouette of a standing animal"></div>
      <h1 class="brand-name">HOPWELL</h1>
      <p class="tagline">If it keeps a drink cold or the party going...we do it!</p>
    </section>

    <section class="card card-back">
      <div class="identity">
        <h2 class="person-name">DALTON PIKES</h2>
        <p class="person-role">Founder and CPO</p>
      </div>
      <div class="divider"></div>
      <div class="contact">
        <p class="phone">
          <svg viewBox="0 0 24 24" aria-hidden="true"><path d="M6.6 10.8a15.1 15.1 0 0 0 6.6 6.6l2.2-2.2a1 1 0 0 1 1-.25 11.4 11.4 0 0 0 3.6.57 1 1 0 0 1 1 1V20a1 1 0 0 1-1 1A17 17 0 0 1 3 4a1 1 0 0 1 1-1h3.5a1 1 0 0 1 1 1c0 1.25.2 2.45.57 3.57a1 1 0 0 1-.25 1z"/></svg>
          555.318.4726
        </p>
        <address class="address">
          412 E. Carver Avenue, Ste 2207<br>
          Tampa, FL. 33917
        </address>
      </div>
    </section>
  </main>
</body>
</html>
```